Financial Services Consultant needs a business card

We need a business card for a new consulting company based in Melbourne called
"Quelbrook Insights". Tagline is Track, Review, Grow
We would like to see business card designs that are in line with the minimal style of the website www.quelbrook-insights.example
The font I have used on the website is Proxima Nova and would like the same or similar font used on the business card with a minimal design in line with the website Two sided with "QUELBROOK INSIGHTS" TRACK, REVIEW, GROW on one side and name, title and contact details on the otther
Updates

Hi All, thanks for your submissions, much appreciated.

I have recently added some colour to my webiste, it is hex #3a7b74 for those that wish to use it
Thanks

Hi all

thanks very much for your design submissions I am very impressed and they are much appreciated.

Interms of general feedback please find below;

Colour: I am trying to stick to a minimal design and colour scheme for my website which is still under construction, up to 3 colours( www.quelbrook-insights.example) it is currently black and white with a small amount of blue/green but I am open to suggestion/interpretations for a consulting company.

Card: I dont mind if it has rounded edges or straight, I was thinking about using a letterpress card if possible

Detail: the detail on the card will include; Name, Title, Mobile, Personal Email, Business Email,Web,Business Address

Once again thanks for submissions

Industry/Entity Type

Business

```html
<!DOCTYPE html>
<html lang="en">
<head>
<meta charset="utf-8">
<title>Quelbrook Insights — Business Card</title>
<link rel="stylesheet" href="https://fonts.googleapis.com/css2?family=Montserrat:wght@600;700&family=Open+Sans:wght@400;600&display=swap">
<style>
  :root {
    --backdrop: #e9e9e7;
    --card: #ffffff;
    --ink: #111111;
    --band: #141414;
    --accent: #7fb7ae;
    --muted: #4a4a4a;
    --paper-shadow: rgba(0, 0, 0, 0.18);
  }
  * { box-sizing: border-box; margin: 0; padding: 0; }
  html, body {
    width: 1200px;
    height: 720px;
    overflow: hidden;
    background: var(--backdrop);
  }
  .stage {
    width: 1200px;
    height: 720px;
    display: flex;
    align-items: center;
    justify-content: center;
    gap: 44px;
  }
  .card {
    position: relative;
    width: 540px;
    height: 309px;
    background: var(--card);
    box-shadow: 0 6px 18px var(--paper-shadow);
    overflow: hidden;
    font-family: "Open Sans", Arial, sans-serif;
    color: var(--ink);
  }

  .wordmark {
    font-family: "Montserrat", Arial, sans-serif;
    font-weight: 700;
    font-size: 27px;
    letter-spacing: 0.16em;
    line-height: 1.2;
    color: var(--ink);
    white-space: nowrap;
  }

  /* Contact side */
  .band {
    position: absolute;
    left: 0;
    width: 100%;
    height: 46px;
    background: var(--band);
    color: #fff;
    display: flex;
    align-items: center;
    justify-content: center;
    font-size: 14px;
  }
  .band--top { top: 0; border-bottom: 3px solid var(--accent); }
  .band--bottom { bottom: 0; border-top: 3px solid var(--accent); }
  .person-name { font-weight: 600; font-size: 15px; }
  .person-title { font-size: 11px; margin-left: 4px; }
  .contact-side .wordmark {
    position: absolute;
    top: 116px;
    left: 0;
    width: 100%;
    text-align: center;
  }
  .contact-row {
    position: absolute;
    top: 198px;
    left: 0;
    width: 100%;
    display: flex;
    justify-content: center;
    gap: 22px;
    font-size: 12.5px;
    color: var(--muted);
  }
  .contact-item { display: flex; align-items: center; gap: 6px; }
  .contact-item svg { width: 12px; height: 12px; }

  /* Brand side */
  .brand-block {
    position: absolute;
    top: 98px;
    left: 50%;
    transform: translateX(-50%);
    display: flex;
    flex-direction: column;
    align-items: flex-end;
  }
  .brand-side .wordmark { font-size: 29px; }
  .tagline {
    margin-top: 4px;
    margin-right: 40px;
    font-size: 15px;
    color: var(--muted);
  }
  .web-short {
    margin-top: 2px;
    font-size: 14px;
    color: var(--muted);
    letter-spacing: 0.06em;
  }
  .web-full {
    position: absolute;
    bottom: 50px;
    left: 0;
    width: 100%;
    text-align: center;
    font-size: 16px;
    letter-spacing: 0.2em;
    color: var(--muted);
  }
  .web-full strong { color: var(--ink); font-weight: 600; }
</style>
</head>
<body>
<main class="stage">
  <article class="card contact-side">
    <header class="band band--top">
      <span class="person-name">Your Name,</span><span class="person-title">Title</span>
    </header>
    <div class="wordmark">QUELBROOK INSIGHTS</div>
    <div class="contact-row">
      <span class="contact-item">
        <svg viewBox="0 0 24 24" aria-hidden="true"><path fill="#4a4a4a" d="M6.6 10.8a15.1 15.1 0 0 0 6.6 6.6l2.2-2.2a1 1 0 0 1 1-.25 11.4 11.4 0 0 0 3.6.6 1 1 0 0 1 1 1V20a1 1 0 0 1-1 1A17 17 0 0 1 3 4a1 1 0 0 1 1-1h3.5a1 1 0 0 1 1 1c0 1.25.2 2.45.6 3.6a1 1 0 0 1-.25 1z"/></svg>
        555-014-2316
      </span>
      <span class="contact-item">
        <svg viewBox="0 0 24 24" aria-hidden="true"><circle cx="12" cy="12" r="10" fill="none" stroke="#4a4a4a" stroke-width="2"/><ellipse cx="12" cy="12" rx="4" ry="10" fill="none" stroke="#4a4a4a" stroke-width="1.6"/><path d="M2 12h20" stroke="#4a4a4a" stroke-width="1.6"/></svg>
        www.quelbrook-insights.example
      </span>
    </div>
    <footer class="band band--bottom">Street Name, City Name, State Zip Code</footer>
  </article>

  <article class="card brand-side">
    <div class="brand-block">
      <div class="wordmark">QUELBROOK INSIGHTS</div>
      <p class="tagline">Track, Review, Grow</p>
      <p class="web-short">quelbrook-insights.example</p>
    </div>
    <p class="web-full">www.<strong>quelbrook-insights</strong>.example</p>
  </article>
</main>
</body>
</html>
```